Thornbury Spa

We are a large Miami Beach spa and salon. I am still building our website but you can use it as a resource to gain a better understanding of who we are ....www.velloraspa-studio.com.

We offer a comprehensive list of services in hair, nails, massage, skin care, tanning, spray tanning and waxing and we offer high quality products for skin care, tanning and hair. We are open 7 days.

We would like to see a clean and simple menu that looks a lot like the one from "The Spa at Larkwood." In particular, we have a copy of a menu from their West Hollywood, CA location that is just beautiful. In the uploaded content you will see a sampling of that menu. We would like to see greys, blacks, silvers, whites and warm colors like reds and oranges. We specifically attempt to remain gender neutral so that we don't attract only girls (with pink colors and flowers etc). The final design should convey a simple, clean, friendly environment and the final product should be sized such that it is 1.) portable and 2.) inexpensive to print. We will be running thousands of these at a time so cost of printing is a consideration.

The booklet consists of two parts: one part is the standard menu with descriptions of services and products and photos etc (think of this as the sales piece that convinces a potential customer to visit) and will be stapled together like you would expect a small menu to be and should resemble the Larkwood menu. The prices should not be included in this part of the booklet that will be printed and stapled. The other part is a single insert and is removable and replaceable. I want this removable insert placed in the last page of the book in a folder pocket or something else that you can think of so that when it's time to change prices here that I am not throwing away all of the booklets....I am only replacing the inserts at the end of the menu booklet. Please design this single page insert so that should a customer remove it from the booklet and keep it, that it stands alone with our name, logo, website and phone number. This page can and probably will have to be 2 sided.

At the back of the booklet, I also want the polices to be printed in one page (think fine print in any sort of business dealing.)

With regard to the look and feel slider of economical v upmarket...we definitely want to convey we deliver upmarket services at reasonable prices. Think, world class services and products at reasonable, everyday prices.

With regard to the uploaded files:
I uploaded both EPS and TIF formats. The colors in those files are not the palette we want at all. The colors we want use for the circular logo must match the standard colors as depicted in the uploaded file "Thornburytanrooms"

Target Market(s)

The target market is the average 20-35 year old in Miami Beach that cares about their appearance. The range of clientele is quite diverse.

Industry/Entity Type

Environment

Requirements
Must have
• It must have elegant and simple photographs that relate to the services being offered. We are selling a service set and an environment...so this menu should be reflect that goal. The logo should be repeated often throughout the book but in subtle ways.

Stock photos are fine as long as they don't seem obviously stock.

Should not have
• Nothing buddha like. Nothing themed. It should be all inclusive and not seek to identify with any particular group or gender.

Nothing that fits the stereotype of "Miami Beach." We want to represent ourselves in the same category as the best spas in the world because we moving everything we do in that direction. Think class!

```html
<!DOCTYPE html>
<html lang="en">
<head>
<meta charset="utf-8">
<title>Thornbury Spa – Tanning Menu Spread</title>
<link rel="stylesheet" href="https://fonts.googleapis.com/css2?family=Source+Sans+3:wght@400;600&family=Open+Sans:wght@300;600&display=swap">
<style>
  :root {
    --paper: #ffffff;
    --ink-black: #050403;
    --skin-light: #d9a57c;
    --skin-mid: #b0744c;
    --skin-dark: #4a2a18;
    --band-grey: rgba(190, 190, 190, 0.72);
    --title-grey: #555555;
    --fine-ink: #1a1a1a;
    --panel-orange: #bc6c33;
    --panel-orange-deep: #b3652f;
    --panel-brown: #6f4627;
    --panel-glow: #d39a6a;
    --text-light: #ffffff;
    --frame-line: rgba(255, 255, 255, 0.85);
  }

  * { margin: 0; padding: 0; box-sizing: border-box; }

  html, body {
    width: 1200px;
    height: 600px;
    overflow: hidden;
    background: var(--paper);
  }

  .spread {
    position: relative;
    width: 1200px;
    height: 600px;
    overflow: hidden;
    font-family: "Source Sans 3", "Myriad Pro", sans-serif;
  }

  /* Left page: photograph area */
  .photo-area {
    position: absolute;
    left: 0;
    top: 0;
    width: 680px;
    height: 600px;
    background:
      radial-gradient(ellipse 120px 330px at 610px 250px, var(--skin-light) 0%, var(--skin-mid) 45%, var(--skin-dark) 80%, transparent 100%),
      radial-gradient(ellipse 90px 140px at 40px 560px, rgba(230,220,200,0.55) 0%, transparent 100%),
      linear-gradient(90deg, var(--ink-black) 0%, #0b0806 60%, #1c110a 100%);
  }

  .title-band {
    position: absolute;
    left: 0;
    top: 465px;
    width: 680px;
    height: 107px;
    background: var(--band-grey);
  }

  .section-title {
    position: absolute;
    left: 104px;
    top: 492px;
    font-family: "Open Sans", sans-serif;
    font-weight: 300;
    font-size: 40px;
    letter-spacing: 13px;
    color: var(--title-grey);
    line-height: 1;
  }

  .section-intro {
    position: absolute;
    left: 370px;
    top: 495px;
    width: 265px;
    font-family: "Open Sans", sans-serif;
    font-weight: 600;
    font-size: 7.4px;
    letter-spacing: 0.9px;
    line-height: 10.2px;
    color: var(--fine-ink);
  }

  /* Right page: orange panel */
  .panel {
    position: absolute;
    left: 0;
    top: 0;
    width: 1200px;
    height: 600px;
  }

  .page-frame {
    position: absolute;
    left: 19px;
    top: 16px;
    width: 1162px;
    height: 565px;
    border: 2px solid var(--frame-line);
    pointer-events: none;
  }

  .service-copy {
    position: absolute;
    left: 705px;
    top: 62px;
    width: 430px;
    color: var(--text-light);
  }

  .service-copy h2 {
    font-size: 11.5px;
    font-weight: 400;
    letter-spacing: 0.1px;
    margin-bottom: 10px;
  }

  .service-copy h3 {
    font-size: 11.5px;
    font-weight: 400;
    margin-bottom: 10px;
  }

  .service-copy p {
    font-size: 8.6px;
    line-height: 14.5px;
  }

  .price-table {
    margin-top: 14px;
    border-collapse: collapse;
    font-size: 8.6px;
    color: var(--text-light);
  }

  .price-table th {
    font-weight: 400;
    text-align: left;
    padding: 0 0 1px 0;
  }

  .price-table td {
    padding: 0;
    line-height: 14.5px;
  }

  .price-table .col-service { width: 262px; }
  .price-table .col-resident { width: 75px; }
  .price-table .col-guest { width: 60px; }

  .session-note { padding-left: 26px; }

  .brand-mark {
    position: absolute;
    left: 1085px;
    top: 552px;
    transform: translateY(-100%);
    display: flex;
    flex-direction: column;
    align-items: center;
    gap: 8px;
  }

  .brand-dot {
    width: 34px;
    height: 34px;
    border-radius: 50%;
    border: 1.5px solid var(--panel-glow);
  }

  .brand-name {
    font-family: "Source Sans 3", sans-serif;
    font-weight: 400;
    font-size: 13px;
    letter-spacing: 2.5px;
    color: var(--panel-glow);
    text-transform: uppercase;
  }
</style>
</head>
<body>
  <main class="spread">
    <div class="photo-area" role="img" aria-label="Photograph of a bronzed torso being airbrush tanned against a black background"></div>

    <div class="title-band"></div>
    <h1 class="section-title">TANNING</h1>
    <p class="section-intro">Tina, conves conduc ta Simis sus, portis, eo esilicie mei potidees? Arbessules curnihil hacchil lesigiti clum et vit; nicaella ponloctur. Imo in tam poste, quam iam re confit. Ego publicesse te mac tenihil</p>

    <svg class="panel" width="1200" height="600" viewBox="0 0 1200 600" aria-hidden="true">
      <defs>
        <linearGradient id="panelFill" x1="0" y1="0" x2="1" y2="1">
          <stop offset="0" stop-color="var(--panel-orange)"/>
          <stop offset="0.55" stop-color="var(--panel-orange-deep)"/>
          <stop offset="1" stop-color="var(--panel-brown)"/>
        </linearGradient>
        <radialGradient id="panelGlow" cx="920" cy="470" r="190" gradientUnits="userSpaceOnUse">
          <stop offset="0" stop-color="var(--panel-glow)" stop-opacity="0.55"/>
          <stop offset="1" stop-color="var(--panel-glow)" stop-opacity="0"/>
        </radialGradient>
      </defs>
      <path d="M665 0 H1200 V600 H549 C625 592 665 545 665 470 Z" fill="url(#panelFill)"/>
      <path d="M665 0 H1200 V600 H549 C625 592 665 545 665 470 Z" fill="url(#panelGlow)"/>
    </svg>

    <div class="page-frame"></div>

    <section class="service-copy">
      <h2>TANNING</h2>
      <h3>CUSTOM AIRBRUSH TANNING</h3>
      <p>The Thornbury Spa is proud to use the Solara Mist system, widely recognized as the industry’s standard for sunless tanning and made popular the world over by Coastline Glow in California. Our approach uses all-natural ingredients to produce a perfect SoBe tan that can last up to 7 days. So whether you are gearing up for a big night on South Beach or just want to look your sun-kissed best year round, our estheticians will customize the look you desire using any of the 5 different spa elixir formulas, alone or in combination, to achieve the perfectly bronzed effect.</p>

      <table class="price-table">
        <thead>
          <tr>
            <th class="col-service"></th>
            <th class="col-resident">Residents</th>
            <th class="col-guest">Hotel Guests</th>
          </tr>
        </thead>
        <tbody>
          <tr>
            <td>Unlimited Solara Membership (1 month)</td>
            <td>$109.00</td>
            <td>$125.00</td>
          </tr>
          <tr>
            <td>Custom Solara Tan <span class="session-note">(1 session)</span></td>
            <td>$49.00</td>
            <td>$55.00</td>
          </tr>
          <tr>
            <td>Exfoliating Dry Body Scrub &amp; Solara Tan</td>
            <td>$79.00</td>
            <td>$90.00</td>
          </tr>
        </tbody>
      </table>
    </section>

    <div class="brand-mark">
      <span class="brand-dot"></span>
      <span class="brand-name">Thornbury Spa</span>
    </div>
  </main>
</body>
</html>
```